Creation of an elegant and modern turnkey Shopify website

Hello,

We are a new company specializing in the sale of above-ground pools. We want to create a turnkey website, ideally using Shopify. For now, we need a "showcase" site, not an e-commerce platform, with four tabs:

Home Page (an overall presentation of the company)
Our Products (an overview of all the above-ground pools we sell)
Our Projects (a page inspired by Instagram to showcase photos of our future projects)
Contact (a page with all our contact information and a contact form)

We are looking to create a highly visual, elegant, and modern website with vibrant splashes of color. We will provide the text, photos (along with instructions on where to place them on each page), and all other necessary information as attachments.

Thank you in advance for your proposals!

The Brisa Lagoon Team

Target Market(s)

Targeted at Swiss customers (a translator will need to be installed for different languages)

Industry/Entity Type

Sale of customised above-ground pools

Coding

Coded - Design and coding required

Font styles to use
Sans Serif

Colors
0094D4
00A9DD
6FCCEA
C7EBF8
E9F6FB
00AB8E
00BBA5
67D7C9
C6EFE9
E9F9F6

Requirements
Must have
• A stunning, elegant and modern look
Nice to have
• Inspiration from the colors of our logo throughout the site, but in an elegant way
Should not have
• An overly classic look for swimming pool sites

```html
<!DOCTYPE html>
<html lang="en">
<head>
<meta charset="utf-8">
<title>Brisa Lagoon – Above-Ground Pools</title>
<link rel="stylesheet" href="https://fonts.googleapis.com/css2?family=Fira+Sans:wght@400;500;600;700&family=Sarabun:wght@400;500&display=swap">
<style>
:root{
  --accent:#00e0f2;
  --ink:#111418;
  --text:#2c2f33;
  --white:#ffffff;
  --footer-bg:#2a241f;
  --head:"Fira Sans", sans-serif;
  --body:"Sarabun", sans-serif;
}
*{box-sizing:border-box;margin:0;padding:0}
html,body{width:1200px;height:2937px;overflow:hidden}
body{position:relative;background:var(--white);font-family:var(--body);color:var(--text)}
.abs{position:absolute}
.eyebrow{font-family:var(--head);font-weight:600;color:var(--accent);font-size:20px;display:flex;align-items:center;gap:8px;text-transform:uppercase}
.eyebrow::before{content:"";width:50px;height:4px;background:var(--accent)}
.btn{display:inline-block;background:var(--accent);color:var(--white);font-family:var(--head);font-weight:600;font-size:15px;text-transform:uppercase;padding:0 23px;line-height:48px}
.wordmark{font-family:var(--head);font-weight:400;line-height:.95;color:var(--accent);text-align:center;letter-spacing:1px}

/* header */
.site-header{left:0;top:0;width:1200px;height:86px;background:rgba(255,255,255,.82);z-index:3}
.site-header .wordmark{left:98px;top:10px;font-size:30px;width:90px}
.main-nav{left:309px;top:34px;display:flex;gap:30px;font-family:var(--head);font-size:16px;text-transform:uppercase;color:#333}
.main-nav .current{color:var(--accent)}
.lang{left:891px;top:33px;display:flex;align-items:center;gap:6px;font-family:var(--head);font-size:14px;color:#333}
.site-header .btn{left:968px;top:19px;line-height:48px}

/* hero */
.hero{left:0;top:0;width:1200px;height:686px;background:linear-gradient(180deg,#3c5a30 0%,#4c6b3c 25%,#3b8fc8 50%,#1e7fd0 70%,#8f9aa0 100%)}
.hero-card{left:553px;top:174px;width:548px;height:393px;background:var(--white);padding:36px 34px}
.hero-card h1{font-family:var(--head);font-weight:600;font-size:35px;line-height:43px;color:var(--ink);margin:18px 0 16px;text-transform:uppercase}
.hero-card h1 span{color:var(--accent)}
.hero-card p{font-size:18px;line-height:27px;color:var(--ink);margin-bottom:20px}
.dots{left:586px;top:624px;display:flex;gap:10px}
.dots i{width:12px;height:12px;border-radius:50%;background:rgba(255,255,255,.5)}
.dots i.on{background:var(--white)}

/* features */
.feature{top:780px;width:330px;text-align:center}
.feature svg{display:block;margin:0 auto 18px}
.feature h3{font-family:var(--head);font-weight:600;font-size:22px;color:var(--ink);margin-bottom:12px;text-transform:uppercase}
.feature p{font-size:15px;line-height:24.5px}

/* why */
.why{left:98px;top:1062px;width:400px}
.why h2{font-family:var(--head);font-weight:600;font-size:31px;line-height:43px;color:var(--ink);margin:10px 0 6px;text-transform:uppercase}
.why h2 span{color:var(--accent)}
.why .lead{font-size:16px;line-height:28px}
.badges{display:flex;gap:28px;margin:20px 0 26px}
.badge{width:188px;text-align:center}
.badge .ring{width:74px;height:74px;border:5px solid var(--accent);border-radius:50%;margin:0 auto 14px;display:flex;align-items:center;justify-content:center}
.badge h4{font-family:var(--head);font-weight:500;font-size:16px;color:var(--ink);margin-bottom:8px}
.badge p{font-size:16px;line-height:28px}
.why-photo{left:535px;top:1065px;width:567px;height:447px;background:linear-gradient(180deg,#3a4a2a 0%,#5d6b44 25%,#2d8ee0 45%,#1d7ed8 100%)}
.why-box{left:597px;top:1361px;width:507px;height:153px;background:var(--white);border:3px solid var(--accent);padding:30px 34px}
.why-box h3{font-family:var(--head);font-weight:500;font-size:25px;color:var(--ink);margin-bottom:10px}
.why-box p{font-size:17px;line-height:28px}

/* services */
.services-head{left:0;top:1620px;width:1200px;text-align:center}
.services-head .eyebrow{justify-content:center}
.services-head h2{font-family:var(--head);font-weight:600;font-size:30px;color:var(--ink);margin:16px 0 14px}
.services-head p{font-size:16px;line-height:28px;width:820px;margin:0 auto}
.service{top:1818px;width:317px;text-align:center}
.service .photo{height:317px}
.service .num{position:absolute;left:17px;top:-20px;width:56px;height:48px;background:var(--white);border:3px solid var(--accent);font-family:var(--head);font-weight:600;font-size:20px;color:var(--ink);line-height:42px}
.service .tag{position:relative;margin:-24px auto 0;width:220px;height:54px;background:var(--white);border:3px solid var(--accent);font-family:var(--head);font-weight:500;font-size:19px;color:var(--ink);line-height:48px}
.service p{font-size:16px;line-height:28.5px;margin-top:22px;padding:0 4px}

/* footer */
.site-footer{left:0;top:2383px;width:1200px;height:554px;background:radial-gradient(ellipse at 55% 55%,#4a3b2c 0%,#2d2620 55%,#1d1916 100%);color:var(--white);text-align:center}
.site-footer .wordmark{position:absolute;left:500px;top:80px;width:200px;font-size:50px}
.socials{position:absolute;left:0;top:228px;width:1200px;display:flex;justify-content:center;gap:18px}
.socials i{width:17px;height:17px;border-radius:50%;background:var(--white)}
.foot-nav{position:absolute;left:0;top:278px;width:1200px;display:flex;justify-content:center;gap:30px;font-family:var(--head);font-size:16px;text-transform:uppercase}
.foot-text{position:absolute;left:300px;top:338px;width:600px;font-family:var(--head);font-size:14px;line-height:26px;text-transform:uppercase}
.foot-rule{position:absolute;left:98px;top:484px;width:1004px;height:1px;background:rgba(255,255,255,.6)}
.copyright{position:absolute;left:0;top:508px;width:1200px;font-family:var(--head);font-size:14px}
</style>
</head>
<body>

<section class="hero abs" role="img" aria-label="Photo of a child in a round above-ground pool in a garden lined with conifers"></section>

<header class="site-header abs">
  <div class="wordmark abs">Brisa<br>Lagoon</div>
  <nav class="main-nav abs">
    <span class="current">Home</span><span>Why Choose Us</span><span>Our Services</span><span>Guaranteed Satisfaction</span>
  </nav>
  <div class="lang abs">
    <svg width="18" height="18" viewBox="0 0 18 18" fill="none" stroke="#333" stroke-width="1.3"><circle cx="9" cy="9" r="7.5"/><ellipse cx="9" cy="9" rx="3.3" ry="7.5"/><path d="M1.5 9h15M3 5h12M3 13h12"/></svg>
    EN
    <svg width="9" height="6" viewBox="0 0 9 6"><path d="M0 0h9L4.5 6z" fill="#333"/></svg>
  </div>
  <a class="btn abs">Contact Us</a>
</header>

<div class="hero-card abs">
  <div class="eyebrow">Welcome To</div>
  <h1>Transform Your Garden with <span>Our Premium</span> Above-Ground Pools!</h1>
  <p>Achieve your dreams with our custom, tailor-made<br>above-ground pools.</p>
  <a class="btn">Contact Us</a>
</div>
<div class="dots abs"><i></i><i class="on"></i><i></i></div>

<div class="feature abs" style="left:68px">
  <svg width="48" height="60" viewBox="0 0 48 60" fill="none" stroke="var(--accent)" stroke-width="1.6"><circle cx="24" cy="22" r="20"/><circle cx="24" cy="22" r="14"/><path d="M24 13l3 6 6 .8-4.5 4.3 1 6.4L24 27.5 18.5 30.5l1-6.4L15 19.8l6-.8z"/><path d="M12 38L6 56l7-3 4 6 6-15M36 38l6 18-7-3-4 6-6-15"/></svg>
  <h3>Superior Quality</h3>
  <p>Each pool is constructed with high-quality materials, ensuring exceptional durability and strength.</p>
</div>
<div class="feature abs" style="left:434px">
  <svg width="60" height="60" viewBox="0 0 60 60" fill="none" stroke="var(--accent)" stroke-width="1.6"><path d="M6 46l10-10 10 10-10 10z"/><path d="M16 36l8-8 10 10-8 8"/><path d="M40 6l2 5 5 2-5 2-2 5-2-5-5-2 5-2zM50 26l1.5 3 3 1.5-3 1.5-1.5 3-1.5-3-3-1.5 3-1.5zM30 16l1 2 2 1-2 1-1 2-1-2-2-1 2-1zM46 40l1 2 2 1-2 1-1 2-1-2-2-1 2-1z"/></svg>
  <h3>Elegant Design</h3>
  <p>Our pools come in a variety of styles and finishes, seamlessly blending into any garden setting.</p>
</div>
<div class="feature abs" style="left:801px">
  <svg width="60" height="60" viewBox="0 0 60 60" fill="none" stroke="var(--accent)" stroke-width="1.6"><path d="M26 3h8l1.5 7 5 2 6-4 5.5 5.5-4 6 2 5 7 1.5v8l-7 1.5-2 5 4 6-5.5 5.5-6-4-5 2L34 57h-8l-1.5-7-5-2-6 4-5.5-5.5 4-6-2-5L3 34v-8l7-1.5 2-5-4-6L13.5 8l6 4 5-2z"/><circle cx="30" cy="30" r="14"/><circle cx="30" cy="30" r="9"/><path d="M25 30l4 4 7-7"/></svg>
  <h3>Easy Installation</h3>
  <p>Enjoy your new oasis quickly with our quickly with our simple simple and fast installation process.</p>
</div>

<section class="why abs">
  <div class="eyebrow">Why Choose Us</div>
  <h2>Our Above-<span>Ground</span><br>Pools?</h2>
  <p class="lead">Imagine an exceptional relaxation and leisure space right in your own backyard.</p>
  <div class="badges">
    <div class="badge">
      <div class="ring"><svg width="32" height="42" viewBox="0 0 48 60" fill="none" stroke="var(--ink)" stroke-width="2"><circle cx="24" cy="22" r="18"/><path d="M24 13l3 6 6 .8-4.5 4.3 1 6.4L24 27.5 18.5 30.5l1-6.4L15 19.8l6-.8z"/><path d="M12 36L7 54l7-3 4 6 5-14M36 36l5 18-7-3-4 6-5-14"/></svg></div>
      <h4>Superior Quality</h4>
      <p>Each pool is constructed with high-quality materials</p>
    </div>
    <div class="badge">
      <div class="ring"><svg width="32" height="42" viewBox="0 0 48 60" fill="none" stroke="var(--ink)" stroke-width="2"><circle cx="24" cy="22" r="18"/><path d="M24 13l3 6 6 .8-4.5 4.3 1 6.4L24 27.5 18.5 30.5l1-6.4L15 19.8l6-.8z"/><path d="M12 36L7 54l7-3 4 6 5-14M36 36l5 18-7-3-4 6-5-14"/></svg></div>
      <h4>Constant Innovation</h4>
      <p>Each pool is constructed with high-quality materials</p>
    </div>
  </div>
  <a class="btn">Contact Us</a>
</section>
<div class="why-photo abs" role="img" aria-label="Photo of a woman swimming in a blue above-ground pool with a beach ball, trees behind"></div>
<div class="why-box abs">
  <h3>Custom and Tailor-Made</h3>
  <p>Create the pool of your dreams with our customization options, tailored to your specific tastes and needs.</p>
</div>

<section class="services-head abs">
  <div class="eyebrow">Our Services</div>
  <h2>We Bring Your Pool Dreams to Life!</h2>
  <p>Lorem ipsum dolor sit amet, consectetur adipiscing elit, sed do eiusmod tempor incididunt ut labore et dolore magna aliqua. Ut enim ad minim veniam, quis nostrud exercitation ullamco laboris nisi ut aliquip ex ea commodo consequat.</p>
</section>

<article class="service abs" style="left:99px">
  <div class="photo" role="img" aria-label="Close photo of the edge and ladder of a round above-ground pool" style="background:linear-gradient(160deg,#3e5a2e 0%,#4f8fc4 30%,#2a86cc 65%,#a9b3bb 100%)"></div>
  <div class="num">01</div>
  <div class="tag">Personalized Services</div>
  <p>We understand that every garden and client is unique. That's why we offer personalized services, from design to installation and after-sales support.</p>
</article>
<article class="service abs" style="left:442px">
  <div class="photo" role="img" aria-label="Photo of a wood-clad above-ground pool on a timber deck in a green garden" style="background:linear-gradient(180deg,#3f6a2c 0%,#5f8d45 28%,#3aa5d8 38%,#a0502a 50%,#c27a52 70%,#b5896c 100%)"></div>
  <div class="num">02</div>
  <div class="tag">Guaranteed Satisfaction</div>
  <p>We understand that every garden and client is unique. That's why we offer personalized services, from design to installation and after-sales support.</p>
</article>
<article class="service abs" style="left:785px">
  <div class="photo" role="img" aria-label="Photo of a steel-frame above-ground pool next to a house in bright sunshine" style="background:linear-gradient(180deg,#dfe6ea 0%,#c9c3b0 30%,#5aa7b4 55%,#2f8d9a 70%,#5b4636 100%)"></div>
  <div class="num">03</div>
  <div class="tag">Contact Us Today</div>
  <p>We understand that every garden and client is unique. That's why we offer personalized services, from design to installation and after-sales support.</p>
</article>

<footer class="site-footer abs" role="img" aria-label="Dimmed background photo of a child floating in a pool at dusk">
  <div class="wordmark">Brisa<br>Lagoon</div>
  <div class="socials"><i></i><i></i><i></i><i></i></div>
  <nav class="foot-nav"><span>Home</span><span>Why Choose Us</span><span>Our Services</span><span>Guaranteed Satisfaction</span></nav>
  <p class="foot-text">Lorem ipsum dolor sit amet consectetur. Feugiat elit ultricies egestas magna sed in eu sed.ultricies aliquet sagittis faucibus et laoreet.</p>
  <div class="foot-rule"></div>
  <p class="copyright">© 2024 - ALL RIGHTS RESERVED</p>
</footer>

</body>
</html>
```